Travel Agency Website - Simple General

Need a 7 page simple design that is pretty repetitive. Need to be able to load quickly that is SEO optimized. Trying to give ideas on what they can do, be personal as we are local, but at the same time come across as professional and get information easily with little burden.

- Landing Page
- Brimwell Vacations Page
- Family Trips
- Road Trips from Texas
- Other Destinations
- About Us Page
- Contact Us Page

Target Market(s)

Families

Coding

Coded - Design and coding required

Number of Pages Required

5+ page

Colors

Designer to choose colors to be used in the design.

Requirements
Must have
• Like it to flow easily with our logo. Use that for colors, etc.

```html
<!DOCTYPE html>
<html lang="en">
<head>
<meta charset="utf-8">
<title>Lark &amp; Lantern Travel — Family Travel Experts</title>
<meta name="viewport" content="width=1200">
<link rel="stylesheet" href="https://fonts.googleapis.com/css2?family=Figtree:wght@400;500;600;700&family=Playfair+Display:ital,wght@1,600;1,700&display=swap">
<style>
:root{
  --teal:#1d5361;
  --teal-deep:#0f2e36;
  --gold:#c1924a;
  --ink:#1f2a30;
  --muted:#4b5a60;
  --mist:#eef2f3;
  --cream:#fdf1e3;
  --white:#ffffff;
}
*{box-sizing:border-box;margin:0;padding:0}
html,body{width:1200px;height:3552px;overflow:hidden}
body{position:relative;font-family:"Figtree",Arial,sans-serif;color:var(--ink);background:var(--white)}
.abs{position:absolute}
.script{font-family:"Playfair Display",Georgia,serif;font-style:italic;font-weight:700}
a{color:inherit;text-decoration:none}

/* header */
.site-header{position:absolute;left:0;top:0;width:1200px;height:99px;background:var(--white);z-index:3}
.brand{position:absolute;left:106px;top:11px;width:118px;height:106px;border-radius:50%;background:var(--white);border:2px solid #d7e3e5;display:flex;align-items:center;justify-content:center;text-align:center;font-weight:700;color:var(--teal);font-size:16px;line-height:1.15;z-index:4}
.topbar{position:absolute;right:106px;top:10px;display:flex;align-items:center;gap:18px;font-size:14px}
.topbar .item{display:flex;align-items:center;gap:10px}
.topbar .item.call{font-weight:600;font-size:15px}
.ico-dot{width:36px;height:36px;border-radius:50%;background:var(--teal);display:flex;align-items:center;justify-content:center}
.social{width:34px;height:34px;border-radius:50%;border:1.5px solid var(--teal);display:inline-block}
.social.filled{background:var(--teal)}
.main-nav{position:absolute;right:106px;top:68px;display:flex;gap:38px;font-size:13px;font-weight:500;letter-spacing:.3px}
.main-nav a.active{color:var(--teal);font-weight:600}

/* hero */
.hero{position:absolute;left:0;top:99px;width:1200px;height:542px;background:linear-gradient(100deg,#0f3a44 0%,#16606a 40%,#3c8a86 62%,#b9a77a 78%,#6c8a4c 100%)}
.hero::after{content:"";position:absolute;inset:0;background:linear-gradient(180deg,rgba(70,90,110,.45) 0%,rgba(0,0,0,0) 30%)}
.hero-inner{position:absolute;left:106px;top:158px;z-index:2;color:var(--white)}
.pill{display:inline-block;background:rgba(20,30,35,.75);border-radius:20px;padding:6px 16px;font-size:12px;font-weight:600;letter-spacing:1px}
.pill b{color:var(--gold);margin:0 6px}
.hero h1{font-size:54px;font-weight:700;margin-top:18px;line-height:1.1}
.hero p{font-size:16px;line-height:22px;margin-top:14px;width:430px}
.btn{display:inline-flex;align-items:center;gap:14px;background:var(--gold);color:var(--white);border-radius:30px;padding:0 6px 0 22px;height:44px;font-size:14px;font-weight:500;letter-spacing:.3px}
.btn .arr{width:32px;height:32px;border-radius:50%;background:var(--white);display:flex;align-items:center;justify-content:center}
.hero .btn{margin-top:26px}

/* headings */
.eyebrow{font-size:13px;color:var(--gold);letter-spacing:.5px;text-transform:uppercase}
.section-title{font-size:41px;font-weight:700;color:var(--teal);line-height:1.05}
.rule{width:48px;height:3px;background:var(--gold)}
.center{text-align:center;left:0;width:1200px}

/* escapes */
.card{position:absolute;top:859px;width:215px;height:275px;border-radius:10px;overflow:hidden;color:var(--white)}
.card .shade{position:absolute;inset:0;background:linear-gradient(180deg,rgba(0,0,0,0) 45%,rgba(0,0,0,.7) 100%)}
.card .tag{position:absolute;left:16px;top:187px;background:var(--gold);border-radius:10px;padding:2px 10px;font-size:11px;font-weight:600}
.card h3{position:absolute;left:15px;top:208px;font-size:21px;font-weight:700}
.card span.sub{position:absolute;left:15px;top:240px;font-size:13px}

/* about */
.about{position:absolute;left:0;top:1225px;width:1200px;height:673px;background:var(--mist)}
.huts{position:absolute;left:0;top:1738px;width:1200px;height:160px;background:linear-gradient(180deg,var(--mist) 0%,#bcd8dd 45%,#8a6a45 70%,#5fb7bc 100%)}
.about-copy{position:absolute;left:608px;top:80px;width:455px;z-index:2}
.about-copy p{font-size:14px;line-height:22.5px;color:var(--ink);margin-top:12px}

/* why */
.why{position:absolute;left:0;top:1898px;width:1200px;height:821px;background:var(--cream)}
.feature{position:absolute;width:285px;height:207px;background:var(--white);border-radius:8px;text-align:center;box-shadow:0 2px 10px rgba(0,0,0,.04)}
.feature svg{margin-top:32px}
.feature h3{font-size:19px;font-weight:600;margin-top:10px}
.feature p{font-size:13.5px;line-height:20px;color:var(--muted);margin-top:8px}

/* cta */
.cta{position:absolute;left:0;top:2719px;width:1200px;height:420px;background:linear-gradient(180deg,#2f6170 0%,#2b5d63 55%,#3b6a4f 100%);color:var(--white);text-align:center}
.cta h2{font-size:52px;font-weight:700;line-height:66px;margin-top:83px}
.cta p{font-size:15.5px;line-height:22px;margin-top:16px}
.cta .btn{margin-top:28px}

/* footer */
.footer{position:absolute;left:0;top:3139px;width:1200px;height:413px;background:var(--teal-deep);color:var(--white)}
.footer .brand{position:absolute;left:106px;top:81px;width:190px;height:165px;font-size:22px}
.fcol{position:absolute;top:89px}
.fcol h4{font-size:16px;font-weight:600;letter-spacing:.3px}
.fcol .rule{width:28px;height:2px;margin-top:8px}
.links{list-style:none;margin-top:14px;font-size:14px}
.links li{height:28px}
.contact-row{display:flex;gap:14px;margin-top:14px;font-size:14px;line-height:22px}
.contact-row .c{width:34px;height:34px;border-radius:50%;border:1px solid #5d7a82;display:flex;align-items:center;justify-content:center;flex:none;margin-top:4px}
.newsletter p{font-size:14px;line-height:22px;margin-top:14px;width:290px}
.email-field{margin-top:22px;width:282px;height:46px;border:1px solid #5d7a82;border-radius:24px;display:flex;align-items:center;justify-content:space-between;padding:0 8px 0 22px;font-size:14px}
.email-field .go{width:32px;height:32px;border-radius:50%;background:var(--gold);display:flex;align-items:center;justify-content:center}
.bottom-line{position:absolute;left:106px;top:350px;width:988px;height:1px;background:#33515a}
.copyright{position:absolute;left:106px;top:374px;font-size:13.5px}
.fsocial{position:absolute;right:106px;top:365px;display:flex;gap:14px}
.fsocial .social{border-color:var(--white)}
.fsocial .social.filled{background:var(--white)}
</style>
</head>
<body>

<header class="site-header">
  <div class="brand">Lark &amp;<br>Lantern<br>Travel</div>
  <div class="topbar">
    <div class="item call">
      <span class="ico-dot"><svg width="16" height="16" viewBox="0 0 24 24"><path fill="#fff" d="M6.6 10.8a15.1 15.1 0 0 0 6.6 6.6l2.2-2.2c.3-.3.7-.4 1-.2 1.1.4 2.3.6 3.6.6.6 0 1 .4 1 1V20c0 .6-.4 1-1 1A17 17 0 0 1 3 4c0-.6.4-1 1-1h3.5c.6 0 1 .4 1 1 0 1.3.2 2.5.6 3.6.1.3 0 .7-.2 1z"/></svg></span>
      CALL 111.111.1111
    </div>
    <div class="item">
      <span class="ico-dot"><svg width="16" height="14" viewBox="0 0 24 20"><rect x="2" y="3" width="20" height="14" rx="2" fill="none" stroke="#fff" stroke-width="2"/><path d="M2 4l10 7 10-7" fill="none" stroke="#fff" stroke-width="2"/></svg></span>
      hello@larklantern.example
    </div>
    <span class="social filled" role="img" aria-label="Social profile"></span>
    <span class="social" role="img" aria-label="Social profile"></span>
  </div>
  <nav class="main-nav">
    <a class="active" href="#">HOME</a><a href="#">BRIMWELL</a><a href="#">FAMILY TRIPS</a><a href="#">ROAD TRIPS</a><a href="#">DESTINATIONS</a><a href="#">ABOUT US</a><a href="#">CONTACT US</a>
  </nav>
</header>

<section class="hero" role="img" aria-label="Coastal cliffs above a turquoise bay with sailboats and a speedboat wake">
  <div class="hero-inner">
    <span class="pill"><b>•</b>FAMILY TRAVEL EXPERTS<b>•</b></span>
    <h1>Wander <span class="script">Together.</span></h1>
    <p>Expertly Curated Family Vacations With A Personal, Local Touch — Creating Moments That Last A Lifetime.</p>
    <a class="btn" href="#">EXPLORE DESTINATIONS <span class="arr"><svg width="14" height="14" viewBox="0 0 14 14"><path d="M3 11L11 3M5 3h6v6" stroke="#c1924a" stroke-width="1.6" fill="none"/></svg></span></a>
  </div>
</section>

<div class="abs center eyebrow" style="top:723px">Begin Your Adventure</div>
<h2 class="abs center section-title" style="top:744px">Discover <span class="script">Dream Escapes</span></h2>
<div class="abs rule" style="left:576px;top:796px"></div>
<p class="abs center" style="top:815px;font-size:15px">Curated adventures for every family rhythm</p>

<article class="card" style="left:141px;background:linear-gradient(160deg,#8fb6cf,#3d6e88 60%,#7a5b3c)" role="img" aria-label="Traveler with sun hat and backpack on a harbor pier">
  <div class="shade"></div><span class="tag">SIGNATURE</span><h3>Brimwell Vacations</h3><span class="sub">Land And Sea</span>
</article>
<article class="card" style="left:375px;background:linear-gradient(160deg,#7f8b6a,#4e5b3c 60%,#3a3027)" role="img" aria-label="Smiling family of hikers outdoors">
  <div class="shade"></div><span class="tag">FOR ALL AGES</span><h3>Family Trips</h3><span class="sub">Bonding &amp; Adventure</span>
</article>
<article class="card" style="left:608px;background:linear-gradient(180deg,#c9a88a,#b0603a 45%,#6d5a4c)" role="img" aria-label="Traveler in a hat on a desert highway">
  <div class="shade"></div><span class="tag">PARTENERED</span><h3>Texas Road Trips</h3><span class="sub">Piney Trail Van Rentals</span>
</article>
<article class="card" style="left:843px;background:linear-gradient(180deg,#3d8fd0,#6fb2cf 45%,#c9c3b4)" role="img" aria-label="Family walking hand in hand on a beach">
  <div class="shade"></div><span class="tag">BEYOND</span><h3>Other Destinations</h3><span class="sub">Beaches &amp; Mountains &amp; Cities</span>
</article>

<section class="about">
  <svg class="abs" style="left:141px;top:79px" width="400" height="420" role="img" aria-label="Woman in a yellow dress overlooking a tropical bay, with an inset of a family outdoors">
    <defs><linearGradient id="g1" x1="0" y1="0" x2="0" y2="1"><stop offset="0" stop-color="#3b8fb8"/><stop offset=".55" stop-color="#4aa3a8"/><stop offset="1" stop-color="#d1a52a"/></linearGradient></defs>
    <circle cx="190" cy="190" r="190" fill="url(#g1)"/>
    <circle cx="315" cy="330" r="88" fill="#fff"/>
    <circle cx="315" cy="330" r="81" fill="#6b5a45"/>
  </svg>
  <div class="about-copy">
    <div class="eyebrow">About</div>
    <h2 class="section-title" style="margin-top:6px">Lark &amp; Lantern <span class="script">Family Travel</span></h2>
    <div class="rule" style="margin-top:12px"></div>
    <p style="margin-top:18px">We assist families with planning trips, organizing itineraries, and selecting destinations that fit their needs. From Brimwell magic to Texas road adventures, let's craft memories that last a lifetime.</p>
    <p>We don't just book trips — we craft story-filled journeys. With deep local partnerships and expert knowledge of family-friendly destinations, every detail is designed to reduce stress and increase wonder. From Brimwell magic to Texas open roads, your next chapter starts here.</p>
    <a class="btn" href="#" style="margin-top:22px">READ MORE <span class="arr"><svg width="14" height="14" viewBox="0 0 14 14"><path d="M3 11L11 3M5 3h6v6" stroke="#c1924a" stroke-width="1.6" fill="none"/></svg></span></a>
  </div>
</section>
<div class="huts" role="img" aria-label="Row of thatched overwater bungalows on a turquoise lagoon"></div>

<section class="why">
  <div class="abs center eyebrow" style="top:74px">Whist</div>
  <h2 class="abs center section-title" style="top:96px">Why <span class="script">Choose Us</span></h2>
  <div class="abs rule" style="left:576px;top:146px"></div>
  <p class="abs center" style="top:165px;font-size:15px">Locally owned, personally crafted — we turn vacations into stories.</p>

  <div class="feature" style="left:141px;top:216px">
    <svg width="54" height="48" viewBox="0 0 54 48"><path d="M4 14l14-5 18 5 14-5v30l-14 5-18-5-14 5z" fill="none" stroke="#1d5361" stroke-width="3"/><path d="M27 4a9 9 0 0 1 9 9c0 7-9 15-9 15s-9-8-9-15a9 9 0 0 1 9-9z" fill="#c1924a"/><circle cx="27" cy="13" r="3" fill="#fff"/></svg>
    <h3>Local Expertise</h3><p>Texas-based family, we know the<br>best road trips &amp; hidden gems.</p>
  </div>
  <div class="feature" style="left:456px;top:216px">
    <svg width="54" height="48" viewBox="0 0 54 48"><rect x="24" y="2" width="6" height="8" fill="#1d5361"/><rect x="16" y="10" width="22" height="10" fill="#1d5361"/><path d="M6 22h42l-6 14H12z" fill="#1d5361"/><path d="M4 42q6-4 12 0t12 0 12 0 12 0" stroke="#c1924a" stroke-width="3" fill="none"/></svg>
    <h3>Ark &amp; Cruise Expert</h3><p>Brimwell World,<br>Land, Cruise Lines.</p>
  </div>
  <div class="feature" style="left:772px;top:216px">
    <svg width="54" height="48" viewBox="0 0 54 48"><rect x="10" y="4" width="28" height="40" rx="3" fill="#1d5361"/><rect x="18" y="1" width="12" height="7" rx="2" fill="#c1924a"/><path d="M15 16h18M15 23h18M15 30h12" stroke="#fff" stroke-width="2.5"/><path d="M40 26v16M32 34h16" stroke="#c1924a" stroke-width="4"/></svg>
    <h3>Personalized Planning</h3><p>Tailored to your family's style,<br>budget and dreams.</p>
  </div>
  <div class="feature" style="left:141px;top:449px">
    <svg width="54" height="48" viewBox="0 0 54 48"><path d="M20 2h16l6 46H12z" fill="#1d5361"/><path d="M28 8v6M28 20v6M28 32v6" stroke="#fff" stroke-width="3"/><circle cx="44" cy="12" r="6" fill="#c1924a"/></svg>
    <h3>Texas Road Trips</h3><p>Texas-based family, we know the<br>best road trips &amp; hidden gems.</p>
  </div>
  <div class="feature" style="left:456px;top:449px">
    <svg width="54" height="48" viewBox="0 0 54 48"><path d="M27 2l12 5v9c0 7-5 12-12 15-7-3-12-8-12-15V7z" fill="#c1924a"/><path d="M21 15l4 4 8-8" stroke="#fff" stroke-width="3" fill="none"/><path d="M4 34l12-8 11 8 11-8 12 8-14 10-9-6-9 6z" fill="#1d5361"/></svg>
    <h3>Trusted Partners</h3><p>Brimwell, Piney Trail Van Rentals,<br>cruise lines &amp; more.</p>
  </div>
  <div class="feature" style="left:772px;top:449px">
    <svg width="54" height="48" viewBox="0 0 54 48"><circle cx="17" cy="12" r="8" fill="#1d5361"/><circle cx="37" cy="12" r="8" fill="#1d5361"/><path d="M3 44v-8a12 12 0 0 1 24 0v8z" fill="#c1924a"/><path d="M27 44v-8a12 12 0 0 1 24 0v8z" fill="#1d5361"/></svg>
    <h3>100% Family Focus</h3><p>We only serve families — that's<br>our heartbeat.</p>
  </div>

  <a class="btn abs" href="#" style="left:480px;top:692px">EXPLORE DESTINATIONS <span class="arr"><svg width="14" height="14" viewBox="0 0 14 14"><path d="M3 11L11 3M5 3h6v6" stroke="#c1924a" stroke-width="1.6" fill="none"/></svg></span></a>
</section>

<section class="cta" role="img" aria-label="Tropical resort grounds with lawns and pathways under a teal wash">
  <h2>Family Travel Planning<br>Made <span class="script">Simple</span></h2>
  <p>We Assist Families With Planning Trips, Organizing Itineraries, And Selecting Destinations That Fit Their<br>Needs. From Brimwell Magic To Texas Road Adventures, Let's Craft Memories That Last A Lifetime.</p>
  <a class="btn" href="#">EXPLORE DESTINATIONS <span class="arr"><svg width="14" height="14" viewBox="0 0 14 14"><path d="M3 11L11 3M5 3h6v6" stroke="#c1924a" stroke-width="1.6" fill="none"/></svg></span></a>
</section>

<footer class="footer">
  <div class="brand">Lark &amp;<br>Lantern<br>Travel</div>
  <div class="fcol" style="left:359px">
    <h4>QUICK LINKS</h4><div class="rule"></div>
    <ul class="links"><li>Home</li><li>Brimwell</li><li>Family Trips</li><li>Road Trips</li><li>Destinations</li><li>About Us</li><li>Contact Us</li></ul>
  </div>
  <div class="fcol" style="left:525px">
    <h4>CONTACT DETAILS</h4><div class="rule"></div>
    <div class="contact-row"><span class="c"><svg width="14" height="16" viewBox="0 0 14 16"><path d="M7 1a5 5 0 0 1 5 5c0 4-5 9-5 9S2 10 2 6a5 5 0 0 1 5-5z" fill="#fff"/><circle cx="7" cy="6" r="2" fill="#0f2e36"/></svg></span><div>402 Cedar Hollow Ln.<br>City Road, AR 12345</div></div>
    <div class="contact-row"><span class="c"><svg width="14" height="14" viewBox="0 0 24 24"><path fill="#fff" d="M6.6 10.8a15.1 15.1 0 0 0 6.6 6.6l2.2-2.2c.3-.3.7-.4 1-.2 1.1.4 2.3.6 3.6.6.6 0 1 .4 1 1V20c0 .6-.4 1-1 1A17 17 0 0 1 3 4c0-.6.4-1 1-1h3.5c.6 0 1 .4 1 1 0 1.3.2 2.5.6 3.6.1.3 0 .7-.2 1z"/></svg></span><div>Phone<br>111.111.1111</div></div>
    <div class="contact-row"><span class="c"><svg width="14" height="12" viewBox="0 0 24 20"><rect x="2" y="3" width="20" height="14" rx="2" fill="#fff"/><path d="M2 4l10 7 10-7" fill="none" stroke="#0f2e36" stroke-width="2"/></svg></span><div>Email<br>hello@larklantern.example</div></div>
  </div>
  <div class="fcol newsletter" style="left:811px">
    <h4>NEWSLETTER SIGN UP</h4><div class="rule"></div>
    <p>Latest Updates, Exclusive Content, &amp; Special Offers? Subscribe To Our Newsletter!</p>
    <div class="email-field">Email Address <span class="go"><svg width="12" height="12" viewBox="0 0 14 14"><path d="M3 11L11 3M5 3h6v6" stroke="#fff" stroke-width="1.8" fill="none"/></svg></span></div>
  </div>
  <div class="bottom-line"></div>
  <div class="copyright">Copyright 2026 Lark &amp; Lantern Travel. All Rights Reserved.</div>
  <div class="fsocial"><span class="social filled" role="img" aria-label="Social profile"></span><span class="social" role="img" aria-label="Social profile"></span></div>
</footer>

</body>
</html>
```